Business Card front and back

I am looking for business card design. I really really like the design file I uploaded named 627788_19250069_3478263_85f427ee_image

Target Market(s)

Corporate Fitness High end Private country club

Industry/Entity Type

Fitness Industry

Contact Information for Business Card

The last image I like as an example I uploaded a bunch of my logos. The file labeled "the signature" is my business card information for you to use

Colors
0054AA
0677BA
7BADD7
CADEEF
E8F1F8

Requirements
Must have
• E-mail sigThe file I uploaded labeled "627788_19250069_3478263_85f427ee_image" with all the plus signs on the back if those could be the logo symbol I uploaded labeled "1 back.png"

```html
<!DOCTYPE html>
<html lang="en">
<head>
<meta charset="utf-8">
<title>Corefit Studio – Business Card</title>
<link href="https://fonts.googleapis.com/css2?family=Poppins:wght@400;500;700&display=swap" rel="stylesheet">
<style>
  :root {
    --stage: #b7b7b7;
    --card-dark: #323232;
    --card-light: #ffffff;
    --ink: #2b2b2b;
    --ink-soft: #1f1f1f;
    --brand-blue: #4a82c8;
    --rule: #8c8c8c;
  }
  * { box-sizing: border-box; margin: 0; padding: 0; }
  html, body { width: 1200px; height: 1200px; overflow: hidden; }
  body {
    background: var(--stage);
    font-family: "Poppins", sans-serif;
    position: relative;
  }
  .card {
    position: absolute;
    top: 303px;
    height: 594px;
    box-shadow: 3px 4px 6px rgba(0,0,0,0.35);
  }
  .card--back {
    left: 201px;
    width: 369px;
    background: var(--card-dark);
    overflow: hidden;
  }
  .tile-grid {
    position: absolute;
    inset: 0;
    display: block;
  }
  .brand-mark {
    position: absolute;
    left: 163px; top: 384px;
    width: 42px; height: 42px;
    background: var(--brand-blue);
  }
  .brand-name {
    position: absolute;
    left: 72px; width: 225px;
    top: 444px;
    text-align: center;
    color: #ffffff;
    font-weight: 700;
    font-size: 17px;
    letter-spacing: 0.6px;
    text-transform: uppercase;
    line-height: 24px;
  }
  .card--front {
    left: 599px;
    width: 364px;
    background: var(--card-light);
    text-align: center;
    color: var(--ink-soft);
  }
  .portrait {
    position: absolute;
    left: 53px; top: 57px;
    width: 249px; height: 253px;
    border-radius: 50%;
    border: 2px solid var(--brand-blue);
    background: radial-gradient(circle at 50% 40%, #9b7e6e 0%, #5a4a42 35%, #2a2c2a 70%, #1e1f1e 100%);
  }
  .name {
    position: absolute;
    left: 0; right: 0; top: 364px;
    font-weight: 700;
    font-size: 22px;
    line-height: 28px;
    color: var(--ink);
  }
  .name__last { color: var(--brand-blue); }
  .role {
    position: absolute;
    left: 0; right: 0; top: 393px;
    font-size: 15px;
    line-height: 20px;
    letter-spacing: 0.5px;
    color: var(--ink);
  }
  .icon-row {
    position: absolute;
    left: 87px; right: 87px; top: 426px;
    display: flex;
    align-items: center;
    gap: 4px;
  }
  .icon-row__rule { flex: 1; height: 1px; background: var(--rule); }
  .icon-row__rule:first-child { margin-right: 4px; }
  .icon-row__rule:last-child { margin-left: 4px; }
  .icon {
    width: 25px; height: 25px;
    background: var(--brand-blue);
    border-radius: 3px;
    display: flex; align-items: center; justify-content: center;
  }
  .contact {
    position: absolute;
    left: 0; right: 0; top: 457px;
    list-style: none;
    font-size: 16.5px;
    line-height: 21px;
  }
  .divider {
    position: absolute;
    left: 88px; right: 81px; top: 530px;
    height: 1px; background: var(--rule);
  }
  .regions {
    position: absolute;
    left: 0; right: 0; top: 541px;
    font-size: 15.5px;
    line-height: 20px;
  }
</style>
</head>
<body>
  <section class="card card--back">
    <svg class="tile-grid" width="369" height="594" viewBox="0 0 369 594" role="img" aria-label="Repeating grid of plain brand tiles shading from light grey to black">
      <defs>
        <linearGradient id="tile-shade" gradientUnits="userSpaceOnUse" x1="369" y1="0" x2="0" y2="594">
          <stop offset="0" stop-color="#a2a2a2"/>
          <stop offset="0.45" stop-color="#6e6e6e"/>
          <stop offset="0.75" stop-color="#333333"/>
          <stop offset="1" stop-color="#080808"/>
        </linearGradient>
        <pattern id="tile-cells" patternUnits="userSpaceOnUse" x="5" y="3" width="75.5" height="54.4">
          <rect x="0" y="0" width="54" height="42" rx="6" fill="url(#tile-shade)"/>
        </pattern>
        <mask id="tile-gaps">
          <rect width="369" height="594" fill="#fff"/>
          <rect x="80" y="380" width="145" height="50" fill="#000"/>
          <rect x="70" y="435" width="230" height="50" fill="#000"/>
        </mask>
      </defs>
      <g mask="url(#tile-gaps)">
        <rect x="0" y="0" width="369" height="594" fill="url(#tile-cells)"/>
      </g>
      <g fill="url(#tile-shade)">
        <rect x="80.5" y="386" width="54" height="42" rx="6"/>
      </g>
    </svg>
    <span class="brand-mark"></span>
    <p class="brand-name">Corefit Studio</p>
  </section>

  <section class="card card--front">
    <div class="portrait" role="img" aria-label="Circular portrait photo of the consultant"></div>
    <h1 class="name">DANE <span class="name__last">MORROW</span></h1>
    <p class="role">CONSULTANT</p>
    <div class="icon-row">
      <span class="icon-row__rule"></span>
      <span class="icon" aria-label="Phone">
        <svg width="16" height="16" viewBox="0 0 16 16" fill="none" stroke="#fff" stroke-width="1.4"><path d="M2 6c0-2 2-3 6-3s6 1 6 3v1h-3V5.5H5V7H2z"/><rect x="4" y="8" width="8" height="5" rx="1"/></svg>
      </span>
      <span class="icon" aria-label="Email">
        <svg width="16" height="16" viewBox="0 0 16 16" fill="none" stroke="#fff" stroke-width="1.3"><rect x="2" y="4" width="12" height="8"/><path d="M2 4l6 5 6-5M2 12l4.5-4M14 12l-4.5-4"/></svg>
      </span>
      <span class="icon" aria-label="Website">
        <svg width="16" height="16" viewBox="0 0 16 16" fill="none" stroke="#fff" stroke-width="1.3"><circle cx="8" cy="8" r="5.5"/><path d="M2.5 8h11M8 2.5c2 2 2 9 0 11M8 2.5c-2 2-2 9 0 11"/></svg>
      </span>
      <span class="icon-row__rule"></span>
    </div>
    <ul class="contact">
      <li>555-014-2837</li>
      <li>dane@corefitstudio.co</li>
      <li>www.corefitstudio.co</li>
    </ul>
    <div class="divider"></div>
    <p class="regions">ND.SD.MN.IA.KS</p>
  </section>
</body>
</html>
```